Website for new dental office

I am Dr. Colin Ashford and am building a new dental practice. I specialize in general dentistry. I am young and have a higher end dental practice incorporating very new technologies and would like my website to reflect that. As many dental patients are older, the website must be very easy to navigate. I would like patients to be able to request appointments, and will eventually add on patient information forms (the health history, etc, that you normally fill out in the practice) from my practice management software, so leave an area for that.

Industry/Entity Type

Building

```html
<!DOCTYPE html>
<html lang="en">
<head>
<meta charset="utf-8">
<title>Ashford Dental</title>
<link rel="stylesheet" href="https://fonts.googleapis.com/css2?family=Open+Sans:wght@400;600;700&family=Roboto+Condensed:wght@400;700&display=swap">
<style>
  :root {
    --blue: #1f8ad6;
    --blue-dark: #1670b6;
    --blue-deep: #2f56a6;
    --ink: #2d3338;
    --muted: #7a828a;
    --line: #e3e6ea;
    --paper: #ffffff;
    --wash: #f3f5f7;
    --photo-a: #c9d6e2;
    --photo-b: #8ea4b8;
  }
  * { box-sizing: border-box; margin: 0; padding: 0; }
  html, body { width: 1200px; height: 684px; overflow: hidden; background: var(--paper); }
  body { font-family: "Open Sans", Arial, sans-serif; color: var(--ink); }

  .site { position: relative; width: 1200px; height: 684px; }
  .wrap { width: 1100px; margin: 0 auto; position: relative; }

  .topbar { height: 26px; border-bottom: 1px solid var(--line); font-size: 11px; color: var(--muted); }
  .topbar .wrap { display: flex; justify-content: flex-end; align-items: center; gap: 18px; height: 26px; }
  .topbar .contact { display: flex; align-items: center; gap: 5px; }
  .topbar svg { width: 11px; height: 11px; fill: var(--muted); }

  .header { height: 68px; }
  .header .wrap { display: flex; justify-content: space-between; align-items: stretch; height: 68px; }
  .brand { display: flex; align-items: center; gap: 10px; font-family: "Open Sans", Arial, sans-serif; font-weight: 700; font-size: 26px; color: var(--blue-dark); }
  .brand-mark { width: 26px; height: 26px; border-radius: 50%; background: var(--blue); }
  .nav { display: flex; align-items: stretch; list-style: none; }
  .nav li { display: flex; align-items: center; padding: 0 16px; font-size: 13px; font-weight: 600; color: var(--ink); }
  .nav li.active { background: var(--blue); color: var(--paper); }

  .hero { position: relative; height: 240px; }
  .hero-photo { position: absolute; inset: 0; background: linear-gradient(100deg, var(--photo-b) 0%, var(--photo-a) 55%, #e8eef3 100%); }
  .hero-band { position: absolute; right: 0; top: 0; width: 100px; height: 100%; background: var(--blue); }
  .hero-copy { position: absolute; left: 50px; top: 56px; }
  .hero-copy .welcome { font-family: "Roboto Condensed", Arial, sans-serif; font-size: 26px; color: var(--paper); }
  .hero-copy h1 { font-family: "Roboto Condensed", Arial, sans-serif; font-weight: 700; font-size: 38px; color: var(--paper); background: rgba(40,50,60,.55); padding: 2px 12px 2px 0; margin-top: 2px; letter-spacing: .5px; }
  .hero-copy .sub { font-size: 15px; color: var(--paper); margin-top: 4px; }

  .booking { position: relative; }
  .tabs { display: flex; height: 34px; }
  .tab { display: flex; align-items: center; gap: 8px; padding: 0 22px; font-size: 15px; }
  .tab-appointment { width: 560px; background: var(--blue); color: var(--paper); }
  .tab-emergency { width: 540px; background: var(--wash); color: var(--blue-dark); }
  .tab svg { width: 16px; height: 16px; fill: currentColor; }

  .panel { background: var(--blue); color: var(--paper); height: 128px; display: grid; grid-template-columns: 300px 340px 460px; padding: 16px 22px 0; }
  .panel h3 { display: flex; align-items: center; gap: 8px; font-size: 14px; font-weight: 600; margin-bottom: 10px; }
  .panel h3 svg { width: 14px; height: 14px; fill: var(--paper); }
  .hours { list-style: none; font-size: 12px; width: 250px; }
  .hours li { display: flex; justify-content: space-between; padding: 5px 0; border-bottom: 1px solid rgba(255,255,255,.35); }
  .timetable p { font-size: 12px; line-height: 1.45; width: 280px; }
  .btn { display: inline-block; background: var(--paper); color: var(--blue-dark); font-size: 11px; padding: 3px 18px; margin-top: 8px; }
  .form { display: grid; grid-template-columns: 190px 190px; gap: 8px 12px; }
  .field { height: 22px; border: 1px solid rgba(255,255,255,.8); font-size: 11px; padding: 3px 8px; }
  .form .btn { grid-column: 2; text-align: center; margin-top: 0; }

  .services-title { height: 46px; display: flex; align-items: center; font-family: "Roboto Condensed", Arial, sans-serif; font-size: 18px; color: var(--ink); }
  .services-title span { color: var(--blue-dark); font-weight: 700; margin-left: 6px; border-bottom: 2px solid var(--blue); }

  .services { display: grid; grid-template-columns: repeat(4, 1fr); gap: 2px; }
  .service-photo { height: 92px; background: linear-gradient(160deg, #f1e4dc, #c9a89a); }
  .service:nth-child(2) .service-photo { background: linear-gradient(160deg, #e8cfc8, #b3675f); }
  .service:nth-child(3) .service-photo { background: linear-gradient(160deg, #e6c8bf, #a9564e); }
  .service:nth-child(4) .service-photo { background: linear-gradient(160deg, #e6e8ea, #a4acb3); }
  .service-caption { height: 46px; padding: 5px 12px; color: var(--paper); background: var(--blue); }
  .service:nth-child(2) .service-caption { background: var(--blue-dark); }
  .service:nth-child(3) .service-caption, .service:nth-child(4) .service-caption { background: var(--blue-deep); }
  .service-caption h4 { font-family: "Roboto Condensed", Arial, sans-serif; font-size: 18px; font-weight: 700; }
  .service-caption p { font-size: 11px; }
</style>
</head>
<body>
<div class="site">
  <div class="topbar">
    <div class="wrap">
      <span>Open Monday to Saturday</span>
      <span class="contact"><svg viewBox="0 0 16 16"><path d="M1 3h14v10H1z M2 4l6 5 6-5" fill="none" stroke="#7a828a" stroke-width="1.4"/></svg>hello@ashforddental.test</span>
      <span class="contact"><svg viewBox="0 0 16 16"><path d="M4 1l3 3-2 2c1 2 3 4 5 5l2-2 3 3-2 3C7 15 1 9 1 3z"/></svg>(555) 014-2290</span>
    </div>
  </div>

  <header class="header">
    <div class="wrap">
      <div class="brand"><span class="brand-mark"></span>Ashford Dental</div>
      <ul class="nav">
        <li class="active">Home</li>
        <li>About Us</li>
        <li>The Practice</li>
        <li>Area of Expertise</li>
        <li>Appointment</li>
        <li>Contact</li>
      </ul>
    </div>
  </header>

  <section class="hero">
    <div class="hero-photo" role="img" aria-label="Photo of the dentist in a bright modern treatment room with a patient in the chair"></div>
    <div class="hero-band"></div>
    <div class="hero-copy">
      <div class="welcome">Welcome to Ashford Dental</div>
      <h1>PROIN GRAVIDA NIBH</h1>
      <div class="sub">Sed quis bibendum auctor, nisi elit</div>
    </div>
  </section>

  <section class="booking wrap">
    <div class="tabs">
      <div class="tab tab-appointment">Make an Appointment</div>
      <div class="tab tab-emergency"><svg viewBox="0 0 16 16"><path d="M1 4h4l1.5-2h3L11 4h4v10H1z M8 6a3 3 0 1 0 0 6a3 3 0 1 0 0-6z" fill-rule="evenodd"/></svg>For Emergency Cases</div>
    </div>
    <div class="panel">
      <div class="working-time">
        <h3><svg viewBox="0 0 16 16"><path d="M8 1a7 7 0 1 0 0 14A7 7 0 1 0 8 1zm0 2a5 5 0 1 1 0 10A5 5 0 1 1 8 3zM7 4h2v4h3v2H7z" fill-rule="evenodd"/></svg>Working Time</h3>
        <ul class="hours">
          <li><span>Monday – Friday</span><span>8.00 – 17.00</span></li>
          <li><span>Saturday</span><span>9.30 – 17.30</span></li>
          <li><span>Sunday</span><span>9.30 – 15.00</span></li>
        </ul>
      </div>
      <div class="timetable">
        <h3><svg viewBox="0 0 16 16"><path d="M1 3h14v12H1zM3 6h10v7H3zM4 1h2v3H4zM10 1h2v3h-2z" fill-rule="evenodd"/></svg>Doctors Timetable</h3>
        <p>Lorem ipsum dolor sit amet, consectetur adipiscing elit, sed do eiusmod tempor incididunt ut labore et dolore.</p>
        <span class="btn">View Timetable</span>
      </div>
      <div class="visit">
        <h3><svg viewBox="0 0 16 16"><path d="M1 3h14v12H1zM3 6h10v7H3zM4 1h2v3H4zM10 1h2v3h-2zM5 8h3v3H5z" fill-rule="evenodd"/></svg>Booking a Visit</h3>
        <div class="form">
          <div class="field">Select Department</div>
          <div class="field">Your Phone</div>
          <div class="field">Full Name</div>
          <div class="field">mm/dd/yyyy</div>
          <span class="btn">Send</span>
        </div>
      </div>
    </div>
  </section>

  <section class="wrap">
    <h2 class="services-title">About<span>OUR SERVICES</span></h2>
    <div class="services">
      <article class="service">
        <div class="service-photo" role="img" aria-label="Photo of a smiling patient"></div>
        <div class="service-caption"><h4>Cosmetic Dentistry</h4><p>Lorem Ipsum. Proin gravida nibh</p></div>
      </article>
      <article class="service">
        <div class="service-photo" role="img" aria-label="Close-up photo of a white smile"></div>
        <div class="service-caption"><h4>Tooth Whitening</h4><p>Lorem Ipsum. Proin gravida nibh</p></div>
      </article>
      <article class="service">
        <div class="service-photo" role="img" aria-label="Close-up photo of a bright smile"></div>
        <div class="service-caption"><h4>Smile Makeover</h4><p>Lorem Ipsum. Proin gravida nibh</p></div>
      </article>
      <article class="service">
        <div class="service-photo" role="img" aria-label="Photo of a dental implant model"></div>
        <div class="service-caption"><h4>Dental Implants</h4><p>Lorem Ipsum. Proin gravida nibh</p></div>
      </article>
    </div>
  </section>
</div>
</body>
</html>
```